NEW Wordpress Website Design for a Dynamic Long Term Healthcare Company in Hawaii

I would like a new website design for my current company, Marlow Health Collective, which has two different brands - Marlow Homecare and Marlow Senior Living. You can see the current website at www.marlowhealth-example.com. The website should be built using Wordpress Software and the Framewise theme. The website should have a local Hawaii island/tropical feel, but look professional for healthcare. I'm looking for something fresh, and want the designer to select colors, styles, etc.

In the Header, on all pages, I would like a menu that includes Home Care, Senior Living, Rates, and About Us.
Under each of the Header Menu Titles, I would like these drop downs included:
Home Care (drop down pages)- Nurse Aide Care, 24-Hour Home Care, Skilled Nursing, Lifestyle Aide, Hospice at Home, Bathing & Meal Service.
Senior Living (drop down pages) - Long-Term Stay, Short-Term Stay.
Rates (drop down page) - Rates.
About Us (drop down pages) - Our Mission, Ohana Talk, About Dana Marlow.

In the footer, on all pages, you should include the address: 248 Pueo Lane, Suite 310, Honolulu, HI 96817. Phone number: 808-555-0172
The footer should also include buttons for a page called Learn, Caregiver Jobs, and each of the service page links to include: Nurse Aide Care, 24-Hour Home Care, Skilled Nursing, Lifestyle Aide, Hospice at Home, Bathing & Meal Service.
Please don't take the current website and redesign a few aspects. I'm looking for a completely different look and feel.

Target Market(s)

40-80 year olds

Industry/Entity Type

Long Term Healthcare

Coding

Coded - Design and coding required

Requirements
Should not have
• Our existing website as a template. We are looking for a complete redesign. Thank you.

```html
<!DOCTYPE html>
<html lang="en">
<head>
<meta charset="utf-8">
<title>Marlow Senior Living</title>
<link href="https://fonts.googleapis.com/css2?family=Poppins:wght@300;400;500;600&family=Libre+Baskerville:wght@400;700&display=swap" rel="stylesheet">
<style>
:root{
  --teal:#2e6f66;
  --teal-dark:#255a53;
  --orange:#f26a2e;
  --yellow:#fdb913;
  --ink:#1c1c1c;
  --mint:#d6e9e5;
  --mint-soft:#e6f1ef;
  --peach:#f3d5cb;
  --blue:#1c6e86;
  --sky:#dfe9ef;
}
*{margin:0;padding:0;box-sizing:border-box}
html,body{width:1200px;height:4054px;overflow:hidden}
body{font-family:'Poppins',sans-serif;color:var(--ink);background:#fff;position:relative}
.abs{position:absolute}

/* Header + hero */
.hero{position:absolute;left:0;top:0;width:1200px;height:539px;
  background:linear-gradient(180deg,#eef3f6 0%,#e4ecf1 55%,#d9e3e6 75%,#e6e2d9 100%)}
.brand{position:absolute;left:142px;top:26px;display:flex;align-items:center;gap:10px}
.brand-dot{width:22px;height:22px;border-radius:50%;background:var(--teal)}
.brand-name{font-size:22px;font-weight:500;color:var(--teal)}
.nav{position:absolute;top:34px;left:529px;font-size:13px;font-weight:500}
.nav span{position:absolute;white-space:nowrap}
.nav span::after{content:"";display:inline-block;width:5px;height:5px;border-right:1.5px solid var(--ink);border-bottom:1.5px solid var(--ink);transform:rotate(45deg);margin-left:7px;position:relative;top:-3px}
.btn-contact{position:absolute;left:945px;top:22px;width:113px;height:41px;border-radius:21px;background:var(--orange);color:#fff;font-size:13px;font-weight:500;display:flex;align-items:center;justify-content:center}
.hero h1{position:absolute;left:142px;top:200px;font-size:44px;font-weight:400;line-height:55px;letter-spacing:.3px}
.hero h1 em{font-style:normal;color:var(--orange);font-weight:600}
.hero p.lead{position:absolute;left:142px;top:333px;width:420px;font-size:13px;line-height:21px}
.btn-start{position:absolute;left:142px;top:399px;width:115px;height:42px;border-radius:21px;background:var(--yellow);font-size:13px;font-weight:500;display:flex;align-items:center;justify-content:center}
.hero-phone{position:absolute;left:277px;top:409px;font-size:15px;font-weight:500;display:flex;align-items:center;gap:9px}

/* Services */
.svc-label{position:absolute;top:1068px;font-family:'Libre Baskerville',serif;font-size:22px;color:var(--teal);text-align:center;width:400px;letter-spacing:.5px}

/* Split */
.split-photo{position:absolute;left:0;top:1181px;width:598px;height:462px;border-top-right-radius:42px;border-bottom-right-radius:42px;
  background:linear-gradient(135deg,#6f8b4c 0%,#9aa9b8 45%,#8b9aa5 70%,#4e6b3c 100%)}
.care-card{position:absolute;top:1240px;width:268px;height:344px;border-radius:30px;background:var(--teal);color:#fff;text-align:center;padding:32px 14px 0}
.care-card h3{font-family:'Libre Baskerville',serif;font-weight:400;font-size:16px;line-height:25px;letter-spacing:.5px}
.care-card p{font-size:12.3px;line-height:21.5px;margin-top:10px}
.care-card .pill{position:absolute;left:20px;right:20px;bottom:22px;height:48px;border-radius:24px;background:#fff;color:var(--ink);font-size:12px;font-weight:600;display:flex;align-items:center;justify-content:center;border:2px solid var(--teal-dark)}

/* About */
.about h2{position:absolute;left:639px;top:1802px;font-family:'Libre Baskerville',serif;font-weight:400;font-size:22px;color:var(--teal);letter-spacing:.5px}
.about p{position:absolute;left:639px;top:1847px;width:420px;font-size:13.5px;line-height:24px}
.btn-outline{position:absolute;border:1.5px solid var(--teal);color:var(--teal);border-radius:26px;font-size:13px;font-weight:600;display:flex;align-items:center;justify-content:center;background:#fff}

/* Testimonials */
.testi{position:absolute;left:0;top:2186px;width:1200px;height:465px;background:var(--teal)}
.testi h2{position:absolute;top:40px;width:100%;text-align:center;font-family:'Libre Baskerville',serif;font-weight:400;color:#fff;font-size:22px}
.testi .sub{position:absolute;top:74px;left:300px;width:600px;text-align:center;color:#fff;font-size:13px;line-height:24px}
.t-card{position:absolute;top:150px;width:290px;height:255px;border-radius:10px;background:#fff;overflow:hidden}
.t-card h4{position:absolute;left:32px;top:28px;font-family:'Libre Baskerville',serif;font-weight:400;font-size:15.5px;color:var(--teal)}
.t-card p{position:absolute;left:32px;top:64px;width:235px;font-size:13.3px;line-height:24px}
.t-foot{position:absolute;left:0;bottom:0;width:100%;height:72px;background:var(--mint-soft)}
.t-avatar{position:absolute;left:38px;top:24px;width:44px;height:44px;border-radius:50%}
.t-name{position:absolute;left:90px;top:26px;font-size:12px;font-weight:600;line-height:17px}
.t-name span{display:block;font-weight:400}
.t-quote{position:absolute;right:36px;top:-18px}

/* Form */
.sched h2{position:absolute;top:2730px;width:1200px;text-align:center;font-family:'Libre Baskerville',serif;font-weight:400;font-size:22px;line-height:36px;color:var(--teal);letter-spacing:.5px}
.form-box{position:absolute;left:142px;top:2835px;width:916px;height:808px;background:#fff;box-shadow:0 2px 14px rgba(0,0,0,.08)}
.f-label{position:absolute;left:69px;font-size:11.5px;font-weight:600}
.f-field{position:absolute;left:69px;width:778px;height:44px;border:1px solid #eceff0;border-radius:3px;background:#fff}
.f-select::after{content:"";position:absolute;right:22px;top:16px;width:7px;height:7px;border-right:1.3px solid #9aa;border-bottom:1.3px solid #9aa;transform:rotate(45deg)}
.f-note{position:absolute;left:72px;top:680px;font-size:13px}
.f-submit{position:absolute;left:376px;top:734px;width:166px;height:46px;border:1px solid #e3e8e8;border-radius:23px;color:var(--teal);font-size:13px;font-weight:600;display:flex;align-items:center;justify-content:center}

/* Footer */
.footer{position:absolute;left:0;top:3685px;width:1200px;height:369px;background:linear-gradient(180deg,#e7eef3 0%,#eef2f4 100%)}
.f-brand{position:absolute;left:142px;top:100px;display:flex;align-items:center;gap:12px}
.f-brand .sq{width:50px;height:50px;border-radius:50%;background:var(--teal)}
.f-brand span{font-size:30px;font-weight:500;color:var(--teal)}
.f-learn{position:absolute;left:142px;top:184px;width:120px;height:40px;border-radius:20px;background:var(--teal);color:#fff;font-size:13px;font-weight:500;display:flex;align-items:center;justify-content:center}
.f-col{position:absolute;top:58px}
.f-col h5{font-size:16px;font-weight:500;color:var(--orange);margin-bottom:12px}
.f-col a{display:block;font-size:12.5px;color:var(--ink);text-decoration:none;line-height:28px;white-space:nowrap}
.f-contact{font-size:12.5px;line-height:20px;display:flex;gap:12px;margin-bottom:12px}
.f-rule{position:absolute;left:142px;top:304px;width:916px;height:1px;background:#c9d3d6}
.f-copy{position:absolute;left:142px;top:325px;font-size:12px}
.socials{position:absolute;left:926px;top:322px;display:flex;gap:11px}
.socials i{display:block;width:25px;height:25px;border-radius:50%;background:var(--orange)}
.f-bar{position:absolute;left:0;bottom:0;width:1200px;height:4px;background:var(--orange)}
</style>
</head>
<body>

<header class="hero">
  <div role="img" aria-label="Soft tropical beach with palm trees in the background" class="abs" style="left:0;top:0;width:1200px;height:539px;background:linear-gradient(180deg,rgba(255,255,255,0) 50%,rgba(200,214,208,.45) 80%,rgba(230,222,206,.6) 100%)"></div>
  <svg class="abs" style="left:0;top:0" width="1200" height="539" aria-hidden="true">
    <ellipse cx="-10" cy="320" rx="75" ry="130" fill="#f0b7a0" opacity=".7"/>
    <ellipse cx="-10" cy="320" rx="90" ry="145" fill="none" stroke="#c9b3a8" stroke-dasharray="3 4"/>
    <circle cx="194" cy="148" r="6" fill="#fdb913"/>
    <circle cx="91" cy="219" r="12" fill="#8fb9cf"/>
    <polygon points="547,150 558,168 536,168" fill="#f26a2e"/>
    <circle cx="643" cy="334" r="21" fill="#fdb913"/>
    <circle cx="497" cy="437" r="13" fill="#f3c3b4"/>
    <circle cx="1109" cy="460" r="31" fill="#1c6e86"/>
    <circle cx="897" cy="314" r="181" fill="none" stroke="#4f5a5c" stroke-width="1.5" stroke-dasharray="6 6"/>
  </svg>

  <div class="brand"><div class="brand-dot"></div><div class="brand-name">Marlow</div></div>
  <nav class="nav">
    <span style="left:0">Home Care</span>
    <span style="left:115px">Senior Living</span>
    <span style="left:238px">Rates</span>
    <span style="left:317px">About Us</span>
  </nav>
  <div class="btn-contact">Contact Us</div>

  <h1>Happiness Is A Cigar<br>Called <em>Senior Care</em></h1>
  <p class="lead">Marlow Homecare provides a variety of professional in-home health care services throughout the entire island of Oahu.</p>
  <div class="btn-start">Get Started</div>
  <div class="hero-phone">
    <svg width="16" height="16" viewBox="0 0 24 24"><path fill="#2e6f66" d="M6.6 10.8a15.1 15.1 0 0 0 6.6 6.6l2.2-2.2c.3-.3.7-.4 1-.2 1.1.4 2.3.6 3.6.6.6 0 1 .4 1 1V20c0 .6-.4 1-1 1A17 17 0 0 1 3 4c0-.6.4-1 1-1h3.5c.6 0 1 .4 1 1 0 1.3.2 2.5.6 3.6.1.3 0 .7-.2 1z"/></svg>
    (808) 555-0172
  </div>

  <div role="img" aria-label="Caregiver in blue scrubs standing with a smiling senior woman" class="abs" style="left:744px;top:161px;width:306px;height:306px;border-radius:50%;background:linear-gradient(160deg,#cfd9df 0%,#8aa2b5 45%,#6b7c8f 70%,#a79582 100%)"></div>
  <div class="abs" style="left:869px;top:287px;width:56px;height:56px;border-radius:50%;background:#fff;display:flex;align-items:center;justify-content:center">
    <div style="width:38px;height:38px;border-radius:50%;background:var(--orange);display:flex;align-items:center;justify-content:center">
      <svg width="14" height="14" viewBox="0 0 14 14"><polygon points="3,1 13,7 3,13" fill="#fff"/></svg>
    </div>
  </div>
  <div role="img" aria-label="Small portrait of a senior man" class="abs" style="left:777px;top:116px;width:52px;height:52px;border-radius:50%;background:#b9a58e;border:3px solid #fff"></div>
  <div role="img" aria-label="Small portrait of a doctor" class="abs" style="left:1032px;top:188px;width:34px;height:34px;border-radius:50%;background:#b8c6cf;border:2px solid #fff"></div>
  <div role="img" aria-label="Small portrait of a senior man in a hat" class="abs" style="left:738px;top:448px;width:52px;height:52px;border-radius:50%;background:#a99a86;border:3px solid #fff"></div>
</header>

<section class="services">
  <svg class="abs" style="left:0;top:650px" width="1200" height="400" aria-hidden="true">
    <g>
      <ellipse cx="300" cy="210" rx="160" ry="120" fill="#d9ebe6" transform="rotate(-20 300 210)"/>
      <ellipse cx="380" cy="160" rx="170" ry="150" fill="#f3d9cf"/>
      <ellipse cx="470" cy="260" rx="100" ry="140" fill="#f3d9cf"/>
      <ellipse cx="420" cy="340" rx="110" ry="60" fill="#d9ebe6"/>
    </g>
    <g transform="translate(493 0)">
      <ellipse cx="300" cy="210" rx="160" ry="120" fill="#d9ebe6" transform="rotate(-20 300 210)"/>
      <ellipse cx="380" cy="160" rx="170" ry="150" fill="#f3d9cf"/>
      <ellipse cx="470" cy="260" rx="100" ry="140" fill="#f3d9cf"/>
      <ellipse cx="420" cy="340" rx="110" ry="60" fill="#d9ebe6"/>
    </g>
  </svg>
  <div role="img" aria-label="Homecare nurse helping a senior man with his shirt" class="abs" style="left:200px;top:700px;width:332px;height:332px;border-radius:50%;background:linear-gradient(135deg,#d7d36c 0%,#c9c56a 40%,#6a9ccb 75%,#8a7a6a 100%)"></div>
  <div role="img" aria-label="Caregiver assisting a senior man with hand weights" class="abs" style="left:693px;top:700px;width:332px;height:332px;border-radius:50%;background:linear-gradient(135deg,#8fbf7a 0%,#c84a44 45%,#4d8fd0 75%,#6f7d6a 100%)"></div>
  <div class="svc-label" style="left:166px">HOMECARE</div>
  <div class="svc-label" style="left:658px">SENIOR LIVING</div>
</section>

<section class="split">
  <div role="img" aria-label="Caregiver in scrubs walking with a senior woman among tropical plants" class="split-photo"></div>
  <div class="care-card" style="left:480px">
    <h3>PROFESSIONAL CARE<br>IN YOUR HOME</h3>
    <p>Marlow Homecare understands that every person's care journey is unique. We tailor our in-home services to meet the diverse nurturing experience of professional quality care and safety within the comfort and convenience of your own home.</p>
    <div class="pill">SCHEDULE CARE ASSESSMENT</div>
  </div>
  <div class="care-card" style="left:790px">
    <h3>TRUSTED CARE<br>IN OUR HOME</h3>
    <p>Marlow Senior Living creates a warm, supportive, and enriching care home environment where seniors can thrive in their golden years. We provide residential care that promotes well-being, connection, and dignity of each individual.</p>
    <div class="pill">SCHEDULE TOUR</div>
  </div>
</section>

<section class="about">
  <svg class="abs" style="left:0;top:1720px" width="620" height="400" aria-hidden="true">
    <ellipse cx="300" cy="210" rx="160" ry="120" fill="#d9ebe6" transform="rotate(-20 300 210)"/>
    <ellipse cx="380" cy="160" rx="170" ry="150" fill="#f3d9cf"/>
    <ellipse cx="470" cy="260" rx="100" ry="140" fill="#f3d9cf"/>
    <ellipse cx="420" cy="340" rx="110" ry="60" fill="#d9ebe6"/>
  </svg>
  <div role="img" aria-label="Three women sitting together on a sofa knitting" class="abs" style="left:200px;top:1768px;width:332px;height:332px;border-radius:50%;background:linear-gradient(135deg,#c8d6cc 0%,#b9a25c 40%,#a8446a 65%,#8bc1b0 100%)"></div>
  <h2>ABOUT MARLOW HOMECARE</h2>
  <p>At Marlow Health Collective, our mission is to provide compassionate and professional long-term healthcare services that empower individuals to maintain their highest level of independence, health, and well-being in the comfort of their own homes or ours, either through our licensed home healthcare agency - Marlow Homecare, or in our Adult Residential Care Home - Marlow Senior Living.</p>
  <div class="btn-outline" style="left:636px;top:2036px;width:169px;height:49px">Read More</div>
</section>

<section class="testi">
  <h2>Our Testimonials</h2>
  <p class="sub">Hear from the families and residents across Oahu who trust Marlow Homecare and Marlow Senior Living every day.</p>

  <div class="t-card" style="left:142px">
    <h4>Like part of our ohana</h4>
    <p>Our caregiver treats Dad with such patience and kindness. He looks forward to every visit, and we finally have peace of mind.</p>
    <div class="t-foot">
      <svg class="t-quote" width="38" height="32" viewBox="0 0 38 32"><path d="M2 2h14v14l-6 14H4l4-14H2z M22 2h14v14l-6 14h-6l4-14h-6z" fill="none" stroke="#2e6f66" stroke-width="1.3"/></svg>
      <div role="img" aria-label="Customer portrait" class="t-avatar" style="background:#7b5a44"></div>
      <div class="t-name">JOHN JAMES<span>Homecare Family</span></div>
    </div>
  </div>
  <div class="t-card" style="left:455px">
    <h4>Truly a home for Mom</h4>
    <p>The staff at Marlow Senior Living know her by name, her routines and her stories. She is safe, happy and well cared for.</p>
    <div class="t-foot">
      <svg class="t-quote" width="38" height="32" viewBox="0 0 38 32"><path d="M2 2h14v14l-6 14H4l4-14H2z M22 2h14v14l-6 14h-6l4-14h-6z" fill="none" stroke="#2e6f66" stroke-width="1.3"/></svg>
      <div role="img" aria-label="Customer portrait" class="t-avatar" style="background:#c9a48c"></div>
      <div class="t-name">DOE JAMES<span>Senior Living Family</span></div>
    </div>
  </div>
  <div class="t-card" style="left:769px">
    <h4>Professional and caring</h4>
    <p>From skilled nursing to meal help, every visit is on time and thorough. I can stay in my own home with real confidence.</p>
    <div class="t-foot">
      <svg class="t-quote" width="38" height="32" viewBox="0 0 38 32"><path d="M2 2h14v14l-6 14H4l4-14H2z M22 2h14v14l-6 14h-6l4-14h-6z" fill="none" stroke="#2e6f66" stroke-width="1.3"/></svg>
      <div role="img" aria-label="Customer portrait" class="t-avatar" style="background:#8a4f4a"></div>
      <div class="t-name">ALINA JAMES<span>Homecare Client</span></div>
    </div>
  </div>
</section>

<section class="sched">
  <h2>SCHEDULE A COMPLIMENTARY<br>CARE CONSULTATION</h2>
  <div class="form-box">
    <div class="f-label" style="top:32px">Name*</div>
    <div class="f-field" style="top:54px"></div>
    <div class="f-label" style="top:120px">Email*</div>
    <div class="f-field" style="top:142px"></div>
    <div class="f-label" style="top:207px">Phone*</div>
    <div class="f-field" style="top:229px"></div>
    <div class="f-label" style="top:295px">How can we help?</div>
    <div class="f-field f-select" style="top:317px"></div>
    <div class="f-label" style="top:382px">Your Comments*</div>
    <div class="f-field" style="top:404px;height:77px"></div>
    <div class="f-label" style="top:505px">How did you hear about us?</div>
    <div class="f-field" style="top:527px"></div>
    <div class="f-label" style="top:592px">May We Email You About This?</div>
    <div class="f-field f-select" style="top:614px"></div>
    <div class="f-note">You agree to receive future emails and understand you may opt-out at any time</div>
    <div class="f-submit">SUBMIT</div>
  </div>
</section>

<footer class="footer">
  <div role="img" aria-label="Faint palm trees over a soft sky" class="abs" style="left:0;top:0;width:1200px;height:369px;background:radial-gradient(ellipse at 35% 40%,rgba(180,196,186,.35),rgba(255,255,255,0) 60%)"></div>
  <div class="f-brand"><div class="sq"></div><span>Marlow</span></div>
  <div class="f-learn">Learn</div>
  <div class="f-col" style="left:372px">
    <h5>Quick Links</h5>
    <a>Home Care</a><a>Senior Living</a><a>Rates</a><a>About Us</a><a>Caregiver Jobs</a>
  </div>
  <div class="f-col" style="left:514px">
    <h5>Services</h5>
    <a>Nurse Aide Care</a><a>24-Hour Home Care</a><a>Skilled Nursing</a><a>Lifestyle Aide</a><a>Hospice at Home</a><a>Bathing &amp; Meal Service</a>
  </div>
  <div class="f-col" style="left:704px">
    <h5>Resources</h5>
    <a>Privacy Policy</a><a>Terms Of Service</a><a>Contact Us</a>
  </div>
  <div class="f-col" style="left:858px">
    <h5>Contact Info</h5>
    <div class="f-contact">
      <svg width="16" height="18" viewBox="0 0 24 24"><path fill="#f26a2e" d="M12 2a7 7 0 0 0-7 7c0 5 7 13 7 13s7-8 7-13a7 7 0 0 0-7-7zm0 9.5A2.5 2.5 0 1 1 12 6.5a2.5 2.5 0 0 1 0 5z"/></svg>
      <span>248 Pueo Lane, Suite 310,<br>Honolulu, HI 96817</span>
    </div>
    <div class="f-contact">
      <svg width="16" height="16" viewBox="0 0 24 24"><path fill="#f26a2e" d="M6.6 10.8a15.1 15.1 0 0 0 6.6 6.6l2.2-2.2c.3-.3.7-.4 1-.2 1.1.4 2.3.6 3.6.6.6 0 1 .4 1 1V20c0 .6-.4 1-1 1A17 17 0 0 1 3 4c0-.6.4-1 1-1h3.5c.6 0 1 .4 1 1 0 1.3.2 2.5.6 3.6.1.3 0 .7-.2 1z"/></svg>
      <span>808-555-0172</span>
    </div>
  </div>
  <div class="f-rule"></div>
  <div class="f-copy">© 2024 Marlow Health Collective. All Rights Reserved.</div>
  <div class="socials" aria-label="Social links"><i></i><i></i><i></i><i></i></div>
  <div class="f-bar"></div>
</footer>

</body>
</html>
```